Global Yoga Apparel Brand Needs a Beautiful Website

We need a website design for a new Yoga brand called Vey. We develop beautiful, stylish, sexy, comfortable yoga leggings, tops, and yoga apparel for women looking to feel their best, look their best and perform their best on and off the yoga mat.
This will go up at http://vey.example/ (which is a landing page right now).
We would like to see simple and clean design where the focus will be on powerful images and clean background space. We will be using Shopify to start building on and here are three sites that we would love to see options based off of the look, layout and feel while making something unique at the same time:
1. Dunt.ca
2. parvasini.com
3. www.k-mole.com
The final design should look clean, beautiful, inspiring, powerful and empowering.
Target Market(s)
mostly Females 21-35 range but will be appealing to women over 35 as well.

```html
<!DOCTYPE html>
<html lang="en">
<head>
<meta charset="utf-8">
<title>Vey — Yoga Apparels</title>
<link rel="stylesheet" href="https://fonts.googleapis.com/css2?family=Mulish:wght@400;600;700;800&display=swap">
<style>
:root{
  --ink:#111;
  --black:#000;
  --topbar:#2e2e2e;
  --bottombar:#222;
  --white:#fff;
  --line:#d9d9d9;
  --card:#f6f6f6;
  --muted:#555;
  --star:#555;
  --star-off:#bbb;
  --band:#f5f5f5;
  --hero-a:#efedea;
  --hero-b:#d9d6d1;
}
*{box-sizing:border-box;margin:0;padding:0}
html,body{width:1200px;height:2663px;overflow:hidden}
body{font-family:"Mulish",sans-serif;color:var(--ink);background:var(--white);position:relative}
a{color:inherit;text-decoration:none}

.topbar{position:absolute;left:0;top:0;width:1200px;height:32px;background:var(--topbar);color:#ddd;font-size:12px}
.topbar-links{position:absolute;right:84px;top:0;height:32px;display:flex;gap:36px;align-items:center}
.topbar-links span{display:flex;align-items:center;gap:8px}

.header{position:absolute;left:0;top:32px;width:1200px;height:98px;background:var(--black);color:var(--white)}
.logo{position:absolute;left:83px;top:12px;font-size:68px;font-weight:600;letter-spacing:1px;line-height:1}
.nav{position:absolute;left:388px;top:49px;display:flex;align-items:center;font-size:16px;font-weight:700}
.nav a{padding:4px 16px;border-left:1px solid #555}
.nav a:first-child{border:2px solid var(--white);border-radius:3px;margin-right:16px;padding:3px 12px}
.nav a:nth-child(2){border-left:none}
.search{position:absolute;left:1084px;top:48px;width:34px;height:28px;background:var(--white);border-radius:3px;display:flex;align-items:center;justify-content:center}

.hero{position:absolute;left:0;top:130px;width:1200px;height:575px;background:linear-gradient(180deg,var(--hero-a),var(--hero-b))}
.hero-photo{position:absolute;left:120px;top:50px;width:1000px;height:500px;background:radial-gradient(ellipse at 40% 45%,rgba(30,30,30,.25),rgba(0,0,0,0) 60%)}
.hero-copy{position:absolute;right:82px;top:122px;text-align:right}
.hero-copy h1{font-size:47px;font-weight:800;letter-spacing:1px}
.hero-copy p{font-size:26px;line-height:1.25;margin-top:8px;color:#222}
.btn-dark{display:inline-flex;align-items:center;justify-content:center;background:var(--black);color:var(--white);font-weight:700}
.hero .btn-dark{width:156px;height:40px;font-size:17px;margin-top:18px}
.slider-arrows{display:flex;gap:2px;justify-content:flex-end;margin-top:20px}
.slider-arrows span{width:17px;height:17px;border:1px solid #333;background:#eee;display:flex;align-items:center;justify-content:center}

.section-title{position:absolute;left:0;width:1200px;text-align:center;font-size:31px;font-weight:700}
.divider{position:absolute;left:517px;width:166px;height:14px}

.categories{position:absolute;left:82px;top:860px;display:grid;grid-template-columns:repeat(4,249px);gap:14px}
.cat-card{height:220px;border:1px solid var(--line);background:var(--card);padding:7px}
.cat-img{height:152px;background:var(--white);border:1px solid var(--line)}
.cat-name{text-align:center;font-size:19px;font-weight:700;margin-top:18px}

.products{position:absolute;left:82px;top:1235px;display:grid;grid-template-columns:repeat(4,249px);column-gap:14px;row-gap:18px}
.product{height:302px;border:1px solid var(--line);background:var(--card);padding:7px 8px}
.product-img{height:152px;background:var(--white);border:1px solid var(--line)}
.product-name{font-size:15px;font-weight:700;margin-top:12px}
.rating{display:flex;align-items:center;gap:18px;font-size:11px;margin-top:6px}
.stars{color:var(--star);letter-spacing:1px;font-size:12px}
.stars i{color:var(--star-off);font-style:normal}
.price{font-size:17px;font-weight:800;margin-top:10px}
.actions{display:flex;gap:5px;margin-top:14px}
.add-cart{display:flex;align-items:center;height:32px;border:1px solid #333;border-radius:4px;background:var(--white);font-size:11px;overflow:hidden}
.add-cart .ico{width:32px;height:100%;display:flex;align-items:center;justify-content:center;border-right:1px solid #333}
.add-cart .lbl{padding:0 11px}
.icon-btn{width:34px;height:32px;border-radius:4px;background:#cfcfcf;display:flex;align-items:center;justify-content:center}

.newsletter{position:absolute;left:0;top:1912px;width:1200px;height:239px;background:var(--band);text-align:center}
.newsletter h2{font-size:25px;font-weight:800;margin-top:58px;letter-spacing:.5px}
.newsletter p{font-size:14px;color:var(--muted);margin-top:10px}
.newsletter .btn-dark{width:154px;height:39px;font-size:17px;margin-top:22px}

.perks{position:absolute;left:257px;top:2206px;display:flex;gap:39px}
.perk{width:203px;height:110px;border:4px double var(--ink);outline:1px dotted #888;outline-offset:-8px;text-align:center;padding-top:16px}
.perk h3{font-size:13px;font-weight:700;margin-top:6px}
.perk p{font-size:11px;margin-top:4px}

.footer{position:absolute;left:0;top:2370px;width:1200px;height:243px;background:var(--black);color:var(--white)}
.footer-col{position:absolute;top:40px}
.footer-col h4{font-size:14px;font-weight:700;padding-bottom:12px;border-bottom:1px solid #333;width:150px}
.footer-col ul{list-style:none;margin-top:12px;font-size:12px;line-height:22.5px}
.footer-col li::before{content:"";display:inline-block;border-left:5px solid var(--white);border-top:4px solid transparent;border-bottom:4px solid transparent;margin-right:10px}
.col-sep{position:absolute;top:30px;width:0;height:190px;border-left:1px dotted #444}
.news-col p{font-size:14px;line-height:20px;margin-top:22px;width:260px}
.news-col .field{margin-top:14px;width:258px;height:31px;background:var(--white);color:#333;font-size:11px;padding:9px 8px}
.news-col .submit{margin-top:10px;width:72px;height:33px;background:#555;border:1px solid #888;font-size:14px;display:flex;align-items:center;justify-content:center}
.footer-logo{position:absolute;left:1002px;top:68px;font-size:66px;font-weight:600;line-height:1}
.social{position:absolute;left:987px;top:162px;display:flex;gap:10px}
.social span{width:26px;height:26px;background:#9a9a9a;border-radius:2px}

.bottombar{position:absolute;left:0;top:2613px;width:1200px;height:50px;background:var(--bottombar);color:#ddd;font-size:13px}
.copyright{position:absolute;left:83px;top:17px}
.accept{position:absolute;right:82px;top:13px;display:flex;align-items:center;gap:6px}
.accept b{font-weight:600;margin-right:6px}
.card{width:36px;height:24px;background:var(--white);color:#333;border-radius:2px;font-size:9px;font-weight:700;display:flex;align-items:center;justify-content:center}
</style>
</head>
<body>

<div class="topbar">
  <div class="topbar-links">
    <span><svg width="14" height="12" viewBox="0 0 14 12"><path d="M0 1h3l2 7h7l2-5H4" fill="none" stroke="#ddd" stroke-width="1.4"/><circle cx="6" cy="10.5" r="1.2" fill="#ddd"/><circle cx="11" cy="10.5" r="1.2" fill="#ddd"/></svg>View Cart (0)</span>
    <span><svg width="12" height="13" viewBox="0 0 12 13"><rect x="1" y="1" width="10" height="11" fill="none" stroke="#ddd" stroke-width="1.4"/><path d="M3 5h6M3 8h6" stroke="#ddd"/></svg>Register</span>
    <span><svg width="13" height="12" viewBox="0 0 13 12"><path d="M7 1h5v10H7M1 6h7M5 3l3 3-3 3" fill="none" stroke="#ddd" stroke-width="1.4"/></svg>Login</span>
  </div>
</div>

<header class="header">
  <div class="logo">vey</div>
  <nav class="nav">
    <a href="#">Home</a><a href="#">About</a><a href="#">Inspiration</a><a href="#">Featured Products</a><a href="#">Blog</a><a href="#">Contact Us</a>
  </nav>
  <div class="search"><svg width="16" height="16" viewBox="0 0 16 16"><circle cx="6.5" cy="6.5" r="4.5" fill="none" stroke="#000" stroke-width="2.2"/><path d="M10 10l4.5 4.5" stroke="#000" stroke-width="2.6"/></svg></div>
</header>

<section class="hero">
  <div class="hero-photo" role="img" aria-label="Woman in a black yoga outfit holding a plank pose"></div>
  <div class="hero-copy">
    <h1>Yoga Apparels</h1>
    <p>Stretchable fabrics enhance<br>yoga postures</p>
    <a class="btn-dark" href="#">Shop Now</a>
    <div class="slider-arrows">
      <span><svg width="7" height="8"><path d="M6 0v8L0 4z" fill="#222"/></svg></span>
      <span><svg width="7" height="8"><path d="M1 0v8l6-4z" fill="#222"/></svg></span>
    </div>
  </div>
</section>

<h2 class="section-title" style="top:752px">Categories</h2>
<svg class="divider" style="top:809px" viewBox="0 0 166 14"><path d="M0 7h74M92 7h74" stroke="#ccc"/><circle cx="83" cy="7" r="5" fill="none" stroke="#ccc" stroke-width="1.5"/></svg>

<div class="categories">
  <div class="cat-card"><div class="cat-img" role="img" aria-label="Grey yoga leggings"></div><div class="cat-name">Yoga leggings</div></div>
  <div class="cat-card"><div class="cat-img" role="img" aria-label="Black sports bra top"></div><div class="cat-name">Yoga tops</div></div>
  <div class="cat-card"><div class="cat-img" role="img" aria-label="Black capri with green waistband"></div><div class="cat-name">Yoga Capri</div></div>
  <div class="cat-card"><div class="cat-img" role="img" aria-label="Black and lime yoga shoes"></div><div class="cat-name">Yoga Shoes</div></div>
</div>

<h2 class="section-title" style="top:1128px">Featured Products</h2>
<svg class="divider" style="top:1179px" viewBox="0 0 166 14"><path d="M0 7h74M92 7h74" stroke="#ccc"/><circle cx="83" cy="7" r="5" fill="none" stroke="#ccc" stroke-width="1.5"/></svg>

<div class="products">
  <div class="product"><div class="product-img" role="img" aria-label="Lime green tank top" style="background:linear-gradient(#fff,#eef6dc)"></div><div class="product-name">Yoga Top</div><div class="rating"><span class="stars">★★★★<i>★</i></span>1 Review(s)</div><div class="price">$16.95</div><div class="actions"><span class="add-cart"><span class="ico"><svg width="12" height="11"><path d="M0 1h2.5l2 6h6l1.5-4H3.5" fill="none" stroke="#000" stroke-width="1.3"/><circle cx="5" cy="9.5" r="1" /><circle cx="10" cy="9.5" r="1"/></svg></span><span class="lbl">Add to Cart</span></span><span class="icon-btn"><svg width="16" height="12"><path d="M1 3h13l-3-2M15 9H2l3 2" fill="none" stroke="#fff" stroke-width="1.5"/></svg></span><span class="icon-btn"><svg width="14" height="12"><path d="M7 11L1.5 5.5A3 3 0 017 2a3 3 0 015.5 3.5z" fill="#fff"/></svg></span></div></div>
  <div class="product"><div class="product-img" role="img" aria-label="Pink patterned capri" style="background:linear-gradient(#fff,#fbe6ef)"></div><div class="product-name">Yoga Capri</div><div class="rating"><span class="stars">★★★★<i>★</i></span>1 Review(s)</div><div class="price">$ 20.00</div><div class="actions"><span class="add-cart"><span class="ico"><svg width="12" height="11"><path d="M0 1h2.5l2 6h6l1.5-4H3.5" fill="none" stroke="#000" stroke-width="1.3"/><circle cx="5" cy="9.5" r="1" /><circle cx="10" cy="9.5" r="1"/></svg></span><span class="lbl">Add to Cart</span></span><span class="icon-btn"><svg width="16" height="12"><path d="M1 3h13l-3-2M15 9H2l3 2" fill="none" stroke="#fff" stroke-width="1.5"/></svg></span><span class="icon-btn"><svg width="14" height="12"><path d="M7 11L1.5 5.5A3 3 0 017 2a3 3 0 015.5 3.5z" fill="#fff"/></svg></span></div></div>
  <div class="product"><div class="product-img" role="img" aria-label="Black yoga leggings" style="background:linear-gradient(#fff,#e9e9e9)"></div><div class="product-name">Yoga Leggings</div><div class="rating"><span class="stars">★★★★<i>★</i></span>1 Review(s)</div><div class="price">$ 22.50</div><div class="actions"><span class="add-cart"><span class="ico"><svg width="12" height="11"><path d="M0 1h2.5l2 6h6l1.5-4H3.5" fill="none" stroke="#000" stroke-width="1.3"/><circle cx="5" cy="9.5" r="1" /><circle cx="10" cy="9.5" r="1"/></svg></span><span class="lbl">Add to Cart</span></span><span class="icon-btn"><svg width="16" height="12"><path d="M1 3h13l-3-2M15 9H2l3 2" fill="none" stroke="#fff" stroke-width="1.5"/></svg></span><span class="icon-btn"><svg width="14" height="12"><path d="M7 11L1.5 5.5A3 3 0 017 2a3 3 0 015.5 3.5z" fill="#fff"/></svg></span></div></div>
  <div class="product"><div class="product-img" role="img" aria-label="Black pant with yellow waistband and bra top" style="background:linear-gradient(#fff,#f1f0e2)"></div><div class="product-name">Yoga T-shirt &amp; Pant</div><div class="rating"><span class="stars">★★★★<i>★</i></span>1 Review(s)</div><div class="price">$ 18.95</div><div class="actions"><span class="add-cart"><span class="ico"><svg width="12" height="11"><path d="M0 1h2.5l2 6h6l1.5-4H3.5" fill="none" stroke="#000" stroke-width="1.3"/><circle cx="5" cy="9.5" r="1" /><circle cx="10" cy="9.5" r="1"/></svg></span><span class="lbl">Add to Cart</span></span><span class="icon-btn"><svg width="16" height="12"><path d="M1 3h13l-3-2M15 9H2l3 2" fill="none" stroke="#fff" stroke-width="1.5"/></svg></span><span class="icon-btn"><svg width="14" height="12"><path d="M7 11L1.5 5.5A3 3 0 017 2a3 3 0 015.5 3.5z" fill="#fff"/></svg></span></div></div>
  <div class="product"><div class="product-img" role="img" aria-label="Hot pink tank top" style="background:linear-gradient(#fff,#fde0ea)"></div><div class="product-name">Yoga T-shirt</div><div class="rating"><span class="stars">★★★★<i>★</i></span>1 Review(s)</div><div class="price">$ 30.95</div><div class="actions"><span class="add-cart"><span class="ico"><svg width="12" height="11"><path d="M0 1h2.5l2 6h6l1.5-4H3.5" fill="none" stroke="#000" stroke-width="1.3"/><circle cx="5" cy="9.5" r="1" /><circle cx="10" cy="9.5" r="1"/></svg></span><span class="lbl">Add to Cart</span></span><span class="icon-btn"><svg width="16" height="12"><path d="M1 3h13l-3-2M15 9H2l3 2" fill="none" stroke="#fff" stroke-width="1.5"/></svg></span><span class="icon-btn"><svg width="14" height="12"><path d="M7 11L1.5 5.5A3 3 0 017 2a3 3 0 015.5 3.5z" fill="#fff"/></svg></span></div></div>
  <div class="product"><div class="product-img" role="img" aria-label="Blue lycra pants" style="background:linear-gradient(#fff,#e0e8fb)"></div><div class="product-name">Yoga Lycra Pants</div><div class="rating"><span class="stars">★★★★<i>★</i></span>1 Review(s)</div><div class="price">$ 28.95</div><div class="actions"><span class="add-cart"><span class="ico"><svg width="12" height="11"><path d="M0 1h2.5l2 6h6l1.5-4H3.5" fill="none" stroke="#000" stroke-width="1.3"/><circle cx="5" cy="9.5" r="1" /><circle cx="10" cy="9.5" r="1"/></svg></span><span class="lbl">Add to Cart</span></span><span class="icon-btn"><svg width="16" height="12"><path d="M1 3h13l-3-2M15 9H2l3 2" fill="none" stroke="#fff" stroke-width="1.5"/></svg></span><span class="icon-btn"><svg width="14" height="12"><path d="M7 11L1.5 5.5A3 3 0 017 2a3 3 0 015.5 3.5z" fill="#fff"/></svg></span></div></div>
  <div class="product"><div class="product-img" role="img" aria-label="Woman in a black cami" style="background:linear-gradient(#fff,#e8e6e4)"></div><div class="product-name">Yoga Women's Cami</div><div class="rating"><span class="stars">★★★★<i>★</i></span>1 Review(s)</div><div class="price">$ 24.95</div><div class="actions"><span class="add-cart"><span class="ico"><svg width="12" height="11"><path d="M0 1h2.5l2 6h6l1.5-4H3.5" fill="none" stroke="#000" stroke-width="1.3"/><circle cx="5" cy="9.5" r="1" /><circle cx="10" cy="9.5" r="1"/></svg></span><span class="lbl">Add to Cart</span></span><span class="icon-btn"><svg width="16" height="12"><path d="M1 3h13l-3-2M15 9H2l3 2" fill="none" stroke="#fff" stroke-width="1.5"/></svg></span><span class="icon-btn"><svg width="14" height="12"><path d="M7 11L1.5 5.5A3 3 0 017 2a3 3 0 015.5 3.5z" fill="#fff"/></svg></span></div></div>
  <div class="product"><div class="product-img" role="img" aria-label="Dark burgundy capri" style="background:linear-gradient(#fff,#ece2e2)"></div><div class="product-name">Yoga Capri</div><div class="rating"><span class="stars">★★★<i>★★</i></span>1 Review(s)</div><div class="price">$ 19.95</div><div class="actions"><span class="add-cart"><span class="ico"><svg width="12" height="11"><path d="M0 1h2.5l2 6h6l1.5-4H3.5" fill="none" stroke="#000" stroke-width="1.3"/><circle cx="5" cy="9.5" r="1" /><circle cx="10" cy="9.5" r="1"/></svg></span><span class="lbl">Add to Cart</span></span><span class="icon-btn"><svg width="16" height="12"><path d="M1 3h13l-3-2M15 9H2l3 2" fill="none" stroke="#fff" stroke-width="1.5"/></svg></span><span class="icon-btn"><svg width="14" height="12"><path d="M7 11L1.5 5.5A3 3 0 017 2a3 3 0 015.5 3.5z" fill="#fff"/></svg></span></div></div>
</div>

<section class="newsletter">
  <h2>BE THE FIRST TO KNOW</h2>
  <p>Sign up for the latest news, new releases and special promotions.</p>
  <a class="btn-dark" href="#">Sign Up</a>
</section>

<div class="perks">
  <div class="perk"><svg width="36" height="24" viewBox="0 0 36 24"><rect x="0" y="2" width="22" height="15" fill="#111"/><path d="M22 7h8l5 6v4H22z" fill="#111"/><circle cx="7" cy="19" r="3.5" fill="#111" stroke="#fff"/><circle cx="28" cy="19" r="3.5" fill="#111" stroke="#fff"/></svg><h3>Free Shipping</h3><p>On order over $ 120.00</p></div>
  <div class="perk"><svg width="30" height="26" viewBox="0 0 30 26"><rect x="2" y="9" width="26" height="6" fill="#111"/><rect x="4" y="15" width="22" height="11" fill="#111"/><rect x="13" y="9" width="4" height="17" fill="#fff"/><path d="M15 9C10 1 5 4 9 9M15 9c5-8 10-5 6 0" fill="none" stroke="#111" stroke-width="2"/></svg><h3>Discount On Orders</h3><p>Vyngle wine consequat odio sed.</p></div>
  <div class="perk"><svg width="28" height="26" viewBox="0 0 28 26"><circle cx="13" cy="8" r="6.5" fill="#111"/><path d="M1 26c0-8 5-11 12-11s12 3 12 11z" fill="#111"/><circle cx="22" cy="20" r="4.5" fill="#fff" stroke="#111" stroke-width="1.5"/></svg><h3>Need On Help</h3><p>On order over $111.00 any Time</p></div>
</div>

<footer class="footer">
  <div class="footer-col" style="left:84px">
    <h4>Quick Links</h4>
    <ul><li>Home</li><li>About</li><li>Inspiration</li><li>Featured Products</li><li>Blog</li><li>Contact Us</li></ul>
  </div>
  <div class="col-sep" style="left:297px"></div>
  <div class="footer-col" style="left:319px">
    <h4>Information</h4>
    <ul><li>About Us</li><li>Customer Service</li><li>New Collection</li><li>Privacy Policy</li><li>Terms &amp; Condition</li><li>Blog</li></ul>
  </div>
  <div class="col-sep" style="left:516px"></div>
  <div class="footer-col news-col" style="left:590px">
    <h4>Newsletter Sign-up</h4>
    <p>Lorem ipsum dolor sit amet, consecte adipiscing elit</p>
    <div class="field">Enter your Email Address</div>
    <div class="submit">Submit</div>
  </div>
  <div class="col-sep" style="left:917px"></div>
  <div class="footer-logo">vey</div>
  <div class="social"><span></span><span></span><span></span><span></span></div>
</footer>

<div class="bottombar">
  <div class="copyright">Copyright © 2016 Vey. All Rights Reserved.</div>
  <div class="accept"><b>We Accept :</b><span class="card">Pava</span><span class="card">Mintra</span><span class="card">Corex</span><span class="card">Ambra</span><span class="card">Paylo</span></div>
</div>

</body>
</html>
```